Branding product image: VELMOT (Golden Papaya) in Plastic Cup (Ready to Eat)

The product is sliced Fruit in Light syrup
Flavour: VELMOT (Golden Papaya)
The temporary product name: VELMOT
I want the product design to be something 'fun', 'natural', and 'colourful'
The design concept could be anything depends on your imagination, but it must be eye catchy and attractive.
Basically, I want you to be creative in designing the logo and the overall graphic design for the label.
The measurement is 20 cm (Length) x 6,5 cm (Height)
The target customers are young and health conscious audiences (10 years - 65 years old).
Create something different. Something extraordinary.
Brief summary about the fruit:
This fruit only grows in certain part of the world. It grows in mountain area that is in tropical climate. The fruit flesh has a yellowish-golden color. It has an extraordinary taste (unlike normal papaya) and it suits very well with any dishes from cold appetizer, white/ red meat, desserts, and cocktails.
I need a packaging design for Fruit Cup productThe product is sliced Fruit in Light syrup.There will be various flavours i.e. apple, lychee, peach, papaya, etc.However, you may design the product using one sample flavour (i.e. papaya) first, as the designs of other flavours could be adjusted afterwards.The temporary product name is: RICCANAI want the product design to be something 'fun', 'natural', and 'colourful'.The design concept could be anything depends on your imagination. Basically, I want you to be creative in designing the logo and the overall graphic design for the label. - Create something different. Something extraordinary -Additional:The measurement is 20cm (Length) x 5cm (Height).The target customers are young audiences (10 years - 35 years old).The product design must stand out in the supermarket shelf.It must be eye catchy and attractive.Thank you,Jordan-PLEASE REFER TO DESIGN SAMPLE ATTACHED TO HAVE A BETTER UNDERSTANDING FOR THE PRODUCT CONCEPT- Added Wednesday, September 17, 2014
Project Deadline Extended Reason: Haven't found a good design. Added Friday, September 19, 2014
Project Deadline Extended Reason: Need more time for designers to finalize and perfect the design.Thank you,Jordan Added Monday, September 29, 2014
Project Deadline Extended Reason: I haven't found a great design yet. Added Tuesday, February 24, 2015
Reason: Getting better designs now. Still Open to new ideas while refining the latest designs from some designers.
Please do your best in submitting other great designs!

```html
<!DOCTYPE html>
<html lang="en">
<head>
<meta charset="utf-8">
<title>DOSUVEL Golden Papaya Label</title>
<link rel="stylesheet" href="https://fonts.googleapis.com/css2?family=Cookie&family=Oswald:wght@500&family=Arimo:wght@700&display=swap">
<style>
  :root {
    --bg-light: #f7faf1;
    --bg-green: #c9dfa6;
    --leaf-green: #8fbf55;
    --bamboo: #c9a66b;
    --bamboo-dark: #9c7a42;
    --badge-red: #d52b2b;
    --ribbon-light: #f3dcc0;
    --ribbon-dark: #c98a48;
    --papaya-orange: #f28c1c;
    --papaya-gold: #f6b733;
    --ink: #141414;
    --white: #ffffff;
  }
  html, body { margin: 0; padding: 0; overflow: hidden; background: #ffffff; }
  .label {
    position: relative;
    width: 1200px;
    height: 402px;
    overflow: hidden;
    background: radial-gradient(ellipse at 50% 55%, var(--bg-light) 0%, #eef4e2 55%, var(--bg-green) 100%);
  }
  .foliage {
    position: absolute;
    top: 10px;
    width: 340px;
    height: 230px;
  }
  .foliage--left { left: 0; background: radial-gradient(ellipse at 30% 20%, var(--leaf-green) 0%, rgba(143,191,85,0.45) 45%, rgba(143,191,85,0) 75%); }
  .foliage--right { right: 0; background: radial-gradient(ellipse at 70% 20%, var(--leaf-green) 0%, rgba(143,191,85,0.45) 45%, rgba(143,191,85,0) 75%); }
  .bamboo {
    position: absolute;
    left: 0;
    width: 1200px;
    background: linear-gradient(180deg, var(--bamboo) 0%, #e2c48c 45%, var(--bamboo-dark) 100%);
  }
  .bamboo--top { top: 0; height: 12px; }
  .bamboo--bottom { bottom: 0; height: 30px; }
  .badge { position: absolute; left: 452px; top: -108px; width: 200px; height: 200px; }
  .badge__name {
    position: absolute;
    left: 452px;
    top: 18px;
    width: 200px;
    text-align: center;
    font-family: "Oswald", sans-serif;
    font-weight: 500;
    font-size: 36px;
    line-height: 1;
    color: var(--white);
  }
  .title { position: absolute; margin: 0; font-family: "Cookie", cursive; font-weight: 400; color: var(--ink); line-height: 1; }
  .title__small { position: absolute; left: 318px; top: 96px; font-size: 62px; }
  .title__large { position: absolute; left: 248px; top: 128px; font-size: 128px; }
  .ribbon { position: absolute; left: 200px; top: 225px; width: 380px; height: 110px; }
  .ribbon__text {
    position: absolute;
    left: 245px;
    top: 272px;
    font-family: "Oswald", sans-serif;
    font-weight: 500;
    font-size: 33px;
    line-height: 1;
    color: var(--white);
    transform: rotate(-4deg);
    transform-origin: left center;
  }
  .fruit-photo {
    position: absolute;
    left: 558px;
    top: 128px;
    width: 470px;
    height: 210px;
    border-radius: 50%;
    background: radial-gradient(ellipse at 55% 45%, var(--papaya-orange) 0%, #f39a26 45%, var(--papaya-gold) 80%, rgba(246,183,51,0) 100%);
  }
  .net-weight {
    position: absolute;
    left: 560px;
    top: 347px;
    font-family: "Arimo", sans-serif;
    font-weight: 700;
    font-size: 17px;
    color: var(--ink);
  }
</style>
</head>
<body>
  <main class="label">
    <div class="foliage foliage--left" role="img" aria-label="Green leaves against a bright sunlit background"></div>
    <div class="foliage foliage--right" role="img" aria-label="Green leaves against a bright sunlit background"></div>
    <div class="bamboo bamboo--top" role="img" aria-label="Bamboo rod border"></div>
    <div class="bamboo bamboo--bottom" role="img" aria-label="Bamboo rod border"></div>

    <svg class="badge" viewBox="0 0 200 200" aria-hidden="true">
      <circle cx="100" cy="100" r="98" fill="var(--badge-red)"/>
    </svg>
    <div class="badge__name">DOSUVEL</div>

    <h1 class="title">
      <span class="title__small">Golden</span>
      <span class="title__large">Papaya</span>
    </h1>

    <svg class="ribbon" viewBox="0 0 380 110" aria-hidden="true">
      <defs>
        <linearGradient id="ribbonFill" x1="0" y1="0" x2="1" y2="0">
          <stop offset="0" stop-color="var(--ribbon-dark)"/>
          <stop offset="0.6" stop-color="#dca569"/>
          <stop offset="1" stop-color="var(--ribbon-light)" stop-opacity="0.3"/>
        </linearGradient>
      </defs>
      <path d="M15 38 C120 28 250 18 380 0 L380 40 C260 58 130 78 25 95 C35 75 30 55 15 38 Z" fill="url(#ribbonFill)"/>
    </svg>
    <div class="ribbon__text">IN LIGHT SYRUP</div>

    <div class="fruit-photo" role="img" aria-label="Two halves of a ripe golden papaya showing orange flesh and dark seeds"></div>

    <div class="net-weight">Net WT 6oz(170g)</div>
  </main>
</body>
</html>
```